REDESIGN MAIN BANNER IMAGE FOR MARKETING WEBSITE

I feel like my main banner image is too busy but I like it but i want to see other options. www.brightlanepromoworks.biz I want a nice professional clean design that goes with current theme of site. Must look professional and show the variety of incentives we offer but not be overwelming.

My business is called Brightlane Promo Works and I provide businesses around the world with marketing incentives that they can use to create exciting promotions and contest and marketing giveaways to help attract more customers.

I provide a variety of different types of incentives such as Vacation Certificates, Dining Vouchers, Hotel Savings Cards, Smart Watches, Etc. that businesses can use in their marketing efforts.

I want my main banner image to reflect the variety of different categories of incentives... that I offer here: https://www.brightlanepromoworks.biz/incentives

We can use images of certificates or images.....I just want the content to be the same:

CONTENT FOR MAIN BANNER IMAGE:
INCREASE LEADS AND SALES OVERNIGHT

CREATE EXCITING MARKETING PROMOTIONS GIVING AWAY SMART DEVICES, VACATION CERTIFICATES, DINING VOUCHERS AND OTHER INCENTIVES TO YOUR CUSTOMERS

GET A FREE SAMPLE PACKAGE FOR A LIMITED TIME ONLY

Target Market(s)

b2b business owners, ceo, president, owner, founder

Industry/Entity Type

Promotional

Requirements
Must have
• Hi guys keep in mind the finished product will have to be 1800x840

Nice to have
• I want a nice professional clean design that goes with current theme of site. Must look professional and show the variety of incentives we offer but not be overwelming.
Should not have

```html
<!DOCTYPE html>
<html lang="en">
<head>
<meta charset="utf-8">
<title>Brightlane Promo Works — Main Banner</title>
<link href="https://fonts.googleapis.com/css2?family=Bebas+Neue&family=Montserrat:wght@400;500;600;700;800&display=swap" rel="stylesheet">
<style>
  :root{
    --stage:#d1d2d4;
    --white:#ffffff;
    --navy:#1d3f86;
    --blue:#1170b8;
    --blue-bright:#1a7fc6;
    --green:#45ad55;
    --teal:#23938f;
    --dark:#4a4a4c;
    --ink:#3c3c3e;
    --brand:#1b6fb5;
  }
  *{box-sizing:border-box;margin:0;padding:0}
  html,body{width:1057px;height:1200px;overflow:hidden;background:var(--white);font-family:"Montserrat",Arial,sans-serif}
  .board{position:relative;width:1057px;height:1200px}

  /* presentation band */
  .stage{position:absolute;left:0;top:0;width:1057px;height:645px;background:var(--stage)}
  .stage-card{position:absolute;left:115px;top:130px;width:806px;height:377px;background:var(--white);box-shadow:0 22px 18px -14px rgba(0,0,0,.45)}
  .stage .banner{left:115px;top:148px;transform:scale(.7635);transform-origin:0 0}

  /* site header */
  .site-header{position:absolute;left:0;top:645px;width:1057px;height:61px;background:var(--white)}
  .brand{position:absolute;left:20px;top:0;height:61px;display:flex;align-items:center;gap:9px;color:var(--brand);font-weight:700;font-size:17px;letter-spacing:.2px}
  .brand-dot{width:22px;height:22px;border-radius:50%;background:var(--brand)}
  .nav{position:absolute;left:282px;top:0;width:451px;height:61px;background:var(--blue-bright);clip-path:polygon(0 0,100% 0,100% 100%,3px 100%,24px 50%)}
  .nav ul{list-style:none;display:flex;position:absolute;left:44px;top:15px}
  .nav li{color:var(--white);font-size:10.5px;font-weight:600;line-height:15px;padding:0 6px;border-left:1px solid rgba(255,255,255,.55)}
  .nav li:first-child{border-left:0}
  .nav li.wide{width:66px}
  .nav li.gap-after{margin-right:10px}
  .account{position:absolute;top:0;width:62px;height:61px;color:var(--white);font-size:10px;font-weight:600;text-align:center;padding-top:12px}
  .account svg{display:block;margin:0 auto 5px}
  .login{left:733px;background:var(--dark)}
  .signup{left:795px;background:var(--blue-bright)}
  .contact{position:absolute;left:857px;top:0;width:200px;height:61px;background:var(--green);color:var(--white);font-size:10px;font-weight:700;display:flex;align-items:center;gap:10px;padding-left:8px;line-height:15px}

  /* banner */
  .banner{position:absolute;width:1036px;height:449px}
  .hero{position:absolute;left:0;top:0;width:635px;height:449px;background:linear-gradient(100deg,var(--navy) 0%,#1a57a3 55%,var(--blue) 100%);overflow:hidden}
  .hero-shape{position:absolute;left:0;top:0}
  .hero-title{position:absolute;left:53px;top:30px;font-family:"Bebas Neue",Impact,sans-serif;font-size:84px;line-height:79px;color:var(--white);letter-spacing:.5px;text-shadow:2px 3px 4px rgba(0,0,0,.25)}
  .hero-copy{position:absolute;left:53px;top:275px;width:560px;font-size:13.6px;font-weight:700;line-height:18.5px;color:var(--white)}
  .cta{position:absolute;left:44px;top:350px;width:422px;height:65px;background:linear-gradient(90deg,var(--green) 0%,#2b8f9a 55%,var(--blue-bright) 100%);color:var(--white);font-size:22px;line-height:26px;padding:7px 0 0 22px;box-shadow:0 10px 8px -6px rgba(0,0,0,.45)}
  .cta strong{font-weight:700}

  .tiles{position:absolute;left:635px;top:0;width:401px;height:449px}
  .tile{position:absolute;left:0;width:401px;height:139px;background:linear-gradient(90deg,var(--green) 0%,var(--teal) 55%,#1c7fb5 100%)}
  .tile-1{top:0;clip-path:polygon(0 0,365px 0,100% 37px,100% 100%,0 100%)}
  .tile-2{top:155px}
  .tile-3{top:310px;clip-path:polygon(0 0,100% 0,100% 102px,365px 100%,0 100%)}
  .incentive{position:absolute;top:12px;width:170px;text-align:center;color:var(--white);font-size:12.5px;line-height:15.5px}
  .incentive:first-child{left:20px}
  .incentive:last-child{left:201px}
  .badge{width:64px;height:64px;margin:0 auto 14px;border-radius:50%;background:var(--white);box-shadow:0 6px 8px rgba(0,0,0,.3);display:flex;align-items:center;justify-content:center}
  .badge svg{width:36px;height:36px;fill:none;stroke:var(--ink);stroke-width:2;stroke-linejoin:round;stroke-linecap:round}
</style>
</head>
<body>
<div class="board">

  <section class="stage">
    <div class="stage-card"></div>
    <div class="banner">
      <div class="hero">
        <svg class="hero-shape" width="635" height="449" viewBox="0 0 635 449">
          <polygon points="0,330 300,150 440,200 630,110 635,449 0,449" fill="#1a3f84" opacity=".45"/>
        </svg>
        <h1 class="hero-title">Increase<br>Leads and Sales<br>Overnight</h1>
        <p class="hero-copy">CREATE EXCITING MARKETING PROMOTIONS GIVINGAWAY SMART DEVICES, VACATION CERTIFICATES, DINING VOUCHERS AND OTHER INCENTIVES TO YOUR CUSTOMERS</p>
        <div class="cta"><strong>Get A Free Sample</strong> Package<br>For A Limited Time Only</div>
      </div>
      <div class="tiles">
        <div class="tile tile-1">
          <div class="incentive"><div class="badge"><svg viewBox="0 0 36 36"><path d="M9 4h13l6 6v22H9z"/><path d="M13 13h11M13 18h11M13 23h11M13 28h8"/></svg></div>Vacation Certificates<br>&amp; Incentives</div>
          <div class="incentive"><div class="badge"><svg viewBox="0 0 36 36"><circle cx="18" cy="18" r="13"/><path d="M23 13l-3 8-7 2 3-8z"/></svg></div>Cruise Certificates<br>&amp; Incentives</div>
        </div>
        <div class="tile tile-2">
          <div class="incentive"><div class="badge"><svg viewBox="0 0 36 36"><path d="M5 17L18 6l13 11"/><path d="M9 14v17h18V14"/><path d="M15 31v-9h6v9"/></svg></div>Resort Certificates<br>&amp; Incentives</div>
          <div class="incentive"><div class="badge"><svg viewBox="0 0 36 36"><path d="M5 8l8-3 10 3 8-3v23l-8 3-10-3-8 3z"/><path d="M13 5v23M23 8v23"/></svg></div>Dining &amp; Restaurant<br>Certificates, Vouchers<br>&amp; Incentives</div>
        </div>
        <div class="tile tile-3">
          <div class="incentive"><div class="badge"><svg viewBox="0 0 36 36"><path d="M20 5h11v11L17 30 6 19z"/><circle cx="25" cy="11" r="2"/></svg></div>Discounts Savings<br>Certificates,<br>Vouchers &amp; Incentives</div>
          <div class="incentive"><div class="badge"><svg viewBox="0 0 36 36"><rect x="5" y="7" width="26" height="18"/><path d="M14 31h8M18 25v6M10 13h9M10 18h6M23 12h4v5h-4z"/></svg></div>Smart Device Certificates<br>&amp; Incentives</div>
        </div>
      </div>
    </div>
  </section>

  <header class="site-header">
    <div class="brand"><span class="brand-dot"></span>Brightlane Promo Works</div>
    <nav class="nav">
      <ul>
        <li>Home</li>
        <li class="wide">The<br>Incentives</li>
        <li>Samples</li>
        <li>Industries</li>
        <li>Testimonials</li>
        <li>Faq</li>
        <li>Contact<br>Us</li>
      </ul>
    </nav>
    <div class="account login">
      <svg width="16" height="16" viewBox="0 0 16 16" fill="#fff"><circle cx="8" cy="4.5" r="3.5"/><path d="M1 16c0-4 3-6.5 7-6.5s7 2.5 7 6.5z"/></svg>LOGIN
    </div>
    <div class="account signup">
      <svg width="16" height="16" viewBox="0 0 16 16"><circle cx="8" cy="8" r="7" fill="none" stroke="#fff" stroke-width="1.5"/><path d="M8 12V5M5 8l3-3 3 3" fill="none" stroke="#fff" stroke-width="1.6"/></svg>SIGN UP
    </div>
    <div class="contact">
      <svg width="16" height="28" viewBox="0 0 16 28"><rect x="1" y="1" width="14" height="26" rx="2.5" fill="none" stroke="#fff" stroke-width="2"/><path d="M1 5h14M1 22h14" stroke="#fff" stroke-width="1.5"/><circle cx="8" cy="24.5" r="1.2" fill="#fff"/></svg>
      <div>CALL US: 1-555-014-2290<br>TEXT US: 1-555-014-7731</div>
    </div>
  </header>

  <section class="banner" style="left:0;top:728px">
    <div class="hero">
      <svg class="hero-shape" width="635" height="449" viewBox="0 0 635 449">
        <polygon points="0,330 300,150 440,200 630,110 635,449 0,449" fill="#1a3f84" opacity=".45"/>
      </svg>
      <h1 class="hero-title">Increase<br>Leads and Sales<br>Overnight</h1>
      <p class="hero-copy">CREATE EXCITING MARKETING PROMOTIONS GIVINGAWAY SMART DEVICES, VACATION CERTIFICATES, DINING VOUCHERS AND OTHER INCENTIVES TO YOUR CUSTOMERS</p>
      <div class="cta"><strong>Get A Free Sample</strong> Package<br>For A Limited Time Only</div>
    </div>
    <div class="tiles">
      <div class="tile tile-1">
        <div class="incentive"><div class="badge"><svg viewBox="0 0 36 36"><path d="M9 4h13l6 6v22H9z"/><path d="M13 13h11M13 18h11M13 23h11M13 28h8"/></svg></div>Vacation Certificates<br>&amp; Incentives</div>
        <div class="incentive"><div class="badge"><svg viewBox="0 0 36 36"><circle cx="18" cy="18" r="13"/><path d="M23 13l-3 8-7 2 3-8z"/></svg></div>Cruise Certificates<br>&amp; Incentives</div>
      </div>
      <div class="tile tile-2">
        <div class="incentive"><div class="badge"><svg viewBox="0 0 36 36"><path d="M5 17L18 6l13 11"/><path d="M9 14v17h18V14"/><path d="M15 31v-9h6v9"/></svg></div>Resort Certificates<br>&amp; Incentives</div>
        <div class="incentive"><div class="badge"><svg viewBox="0 0 36 36"><path d="M5 8l8-3 10 3 8-3v23l-8 3-10-3-8 3z"/><path d="M13 5v23M23 8v23"/></svg></div>Dining &amp; Restaurant<br>Certificates, Vouchers<br>&amp; Incentives</div>
      </div>
      <div class="tile tile-3">
        <div class="incentive"><div class="badge"><svg viewBox="0 0 36 36"><path d="M20 5h11v11L17 30 6 19z"/><circle cx="25" cy="11" r="2"/></svg></div>Discounts Savings<br>Certificates,<br>Vouchers &amp; Incentives</div>
        <div class="incentive"><div class="badge"><svg viewBox="0 0 36 36"><rect x="5" y="7" width="26" height="18"/><path d="M14 31h8M18 25v6M10 13h9M10 18h6M23 12h4v5h-4z"/></svg></div>Smart Device Certificates<br>&amp; Incentives</div>
      </div>
    </div>
  </section>

</div>
</body>
</html>
```